Vindgerdi - Start-up company selling electricity

Hello let me tell you about Vindgerdi.

Vindgerdi is start-up company selling electricity in Iceland. The operations of the company consist of making power usage forecasts for our customers, purchasing the electricity wholesale from the energy producers, and selling the electricity to the consumer. We are focused on tech by using optimization and machine learning to minimize electricity prices to our customers. Our marketing strategy is to portray a tech company mindset and to show dedication to driving down the electricity price on the market.

We need your help to make our website pop. Possible concepts to work with are as follows:

- Iceland the land of ice and fire
- Green energy
- Innovation
- Tech and data science

Link to our website: https://prufa.vindgerdi-example.is/
We are open to ideas.
Thank you!

Target Market(s)

Electricity consumers both homes and companies.

Number of Pages Required

1 page

Font styles to use
Serif
Sans Serif

```html
<!DOCTYPE html>
<html lang="en">
<head>
<meta charset="utf-8">
<title>Vindgerdi – Let's make the electricity system smarter together</title>
<link href="https://fonts.googleapis.com/css2?family=Crimson+Pro:wght@600;700&family=Source+Sans+3:wght@400;600&display=swap" rel="stylesheet">
<style>
:root{
  --red:#9b2b24;
  --red-panel:#a8352c;
  --navy:#1b3363;
  --navy-panel:#1f3a6b;
  --ink:#222222;
  --white:#ffffff;
  --black:#000000;
  --footer:#2a2a2a;
  --line:#8d8d8d;
  --serif:"Crimson Pro", Georgia, serif;
  --sans:"Source Sans 3", Arial, sans-serif;
}
*{margin:0;padding:0;box-sizing:border-box}
html,body{width:1200px;height:2850px;overflow:hidden;background:var(--white)}
body{position:relative;font-family:var(--sans);color:var(--ink)}
.abs{position:absolute}

/* header */
.brand{left:173px;top:40px;display:flex;align-items:center;gap:16px}
.brand-dot{width:40px;height:40px;border-radius:50%;background:var(--navy)}
.brand-name{font-family:var(--serif);font-weight:700;font-size:50px;color:var(--red);letter-spacing:1px;line-height:1}
.contact{display:flex;align-items:center;gap:8px;font-size:18px;font-weight:600;color:var(--navy)}
.contact-icon{width:40px;height:40px;border-radius:50%;display:flex;align-items:center;justify-content:center}
.contact-icon.red{background:var(--red)}
.contact-icon.navy{background:var(--navy)}
.header-contacts{right:172px;top:26px;display:flex;gap:12px}
.nav{right:172px;top:96px;display:flex;gap:15px;font-size:15px;font-weight:600;color:var(--navy)}

/* hero */
.hero{left:0;top:147px;width:1200px;height:723px;background:var(--black);overflow:hidden}
.hero-title{width:100%;top:75px;text-align:center;font-family:var(--serif);font-weight:700;font-size:92px;color:var(--white);letter-spacing:2px;line-height:1}
.hero-sub{width:100%;top:180px;text-align:center;font-size:20px;font-weight:600;color:var(--white)}
.hero-visual{left:110px;top:240px;width:980px;height:330px;background:linear-gradient(180deg,#0d1a36 0%,#142a55 50%,#0b1630 100%)}
.hero-wave{left:0;top:543px}

/* about */
.about-eyebrow{left:173px;top:955px;font-family:var(--serif);font-weight:700;font-size:26px;color:var(--navy)}
.about-title{left:173px;top:983px;font-family:var(--serif);font-weight:700;font-size:38px;color:var(--red)}
.about-text{left:173px;top:1036px;width:455px;font-size:15px;line-height:31.5px;text-align:justify}
.about-text p+p{margin-top:3px}
.btn-dark{left:173px;top:1248px;width:133px;height:52px;border-radius:26px;background:linear-gradient(90deg,var(--red),var(--navy));color:var(--white);font-family:var(--serif);font-weight:600;font-size:18px;display:flex;align-items:center;justify-content:center}
.about-visual{left:775px;top:950px;width:253px;height:383px;border-radius:126px 126px 126px 126px / 200px 200px 126px 126px;background:linear-gradient(160deg,#6e8fae 0%,#2d4f7e 55%,#142a52 100%)}

/* panels */
.panel{top:1420px;height:560px;width:600px;color:var(--white)}
.panel-price{left:0;background:linear-gradient(135deg,#b0463a 0%,var(--red-panel) 55%,#96291f 100%)}
.panel-business{left:600px;background:linear-gradient(135deg,#2a4a7e 0%,var(--navy-panel) 60%,#173062 100%)}
.panel-icon{top:70px}
.panel-title{top:178px;font-family:var(--serif);font-weight:700;font-size:36px;letter-spacing:.5px}
.panel-price .abs{left:173px}
.panel-business .abs{left:34px}
.price-pills{top:240px;display:flex;gap:12px}
.price-pill{width:191px;height:65px;border-radius:33px;background:var(--white);color:var(--red);display:flex;align-items:baseline;justify-content:center;gap:10px;padding-top:10px;font-family:var(--serif)}
.price-value{font-size:38px;font-weight:700;line-height:1}
.price-unit{font-size:16px;font-weight:600}
.price-label{top:324px;font-family:var(--serif);font-weight:700;font-size:23px}
.price-link{top:362px;font-family:var(--serif);font-weight:700;font-size:27px;text-decoration:underline}
.btn-light{top:429px;width:152px;height:58px;border-radius:29px;background:var(--white);color:var(--red);font-family:var(--serif);font-weight:600;font-size:19px;display:flex;align-items:center;justify-content:center}
.biz-heading{font-family:var(--serif);font-weight:700;font-size:27px;text-decoration:underline}
.biz-text{width:394px;font-size:14.5px;line-height:26px;text-align:justify}

/* faq */
.faq-eyebrow{width:100%;top:2058px;text-align:center;font-family:var(--serif);font-weight:700;font-size:26px;color:var(--navy)}
.faq-title{width:100%;top:2087px;text-align:center;font-family:var(--serif);font-weight:700;font-size:39px;color:var(--red)}
.faq-list{left:284px;top:2172px;width:632px;list-style:none}
.faq-item{height:68px;border:2px solid var(--line);border-radius:34px;display:flex;align-items:center;justify-content:space-between;padding:0 4px 0 24px;font-size:18px;margin-bottom:14.5px}
.faq-toggle{width:55px;height:55px;border-radius:50%;background:var(--red);display:flex;align-items:center;justify-content:center}

/* footer */
.footer{left:0;top:2563px;width:1200px;height:287px;background:var(--footer);color:var(--white)}
.footer-brand{left:173px;top:90px;display:flex;align-items:center;gap:20px}
.footer-brand .brand-dot{width:52px;height:52px;background:var(--white)}
.footer-brand .brand-name{font-size:64px;color:var(--white)}
.footer-contacts{left:785px;top:70px;display:flex;flex-direction:column;gap:12px}
.footer-contacts .contact{color:var(--white)}
.footer-contacts .contact-icon{background:var(--white)}
.footer-rule{left:173px;top:209px;width:855px;height:1px;background:var(--line)}
.copyright{width:100%;top:237px;text-align:center;font-size:15px;font-weight:600}
</style>
</head>
<body>

<header>
  <div class="abs brand">
    <span class="brand-dot"></span>
    <span class="brand-name">VINDGERDI</span>
  </div>
  <div class="abs header-contacts">
    <div class="contact">
      <span class="contact-icon red"><svg width="20" height="20" viewBox="0 0 24 24" fill="none" stroke="#fff" stroke-width="2"><path d="M5 3h4l2 5-3 2a11 11 0 0 0 6 6l2-3 5 2v4a2 2 0 0 1-2 2A17 17 0 0 1 3 5a2 2 0 0 1 2-2z"/></svg></span>
      555-0142
    </div>
    <div class="contact">
      <span class="contact-icon navy"><svg width="20" height="20" viewBox="0 0 24 24" fill="none" stroke="#fff" stroke-width="2"><rect x="3" y="5" width="18" height="14" rx="1"/><path d="M3 6l9 7 9-7"/></svg></span>
      hallo@vindgerdi-example.is
    </div>
  </div>
  <nav class="abs nav"><span>Home</span><span>Terms of business</span><span>Question &amp; Answer</span><span>About Vindgerdi</span></nav>
</header>

<section class="abs hero">
  <div class="abs hero-visual" role="img" aria-label="Glowing battery filled with solar panels and wind turbines, with green electric arcs on both sides"></div>
  <h1 class="abs hero-title">VINDGERDI</h1>
  <p class="abs hero-sub">Let's make the electricity system smarter together</p>
  <svg class="abs hero-wave" width="1200" height="180" viewBox="0 0 1200 180">
    <defs>
      <linearGradient id="waveBand" x1="0" x2="1" y1="0" y2="0">
        <stop offset="0" stop-color="#9b2b24"/>
        <stop offset=".45" stop-color="#7a2a3a"/>
        <stop offset=".6" stop-color="#1b3363"/>
        <stop offset="1" stop-color="#1b3363"/>
      </linearGradient>
    </defs>
    <path d="M0,92 C200,180 420,150 700,62 C900,2 1050,20 1200,112 L1200,180 L0,180Z" fill="#fff"/>
    <path d="M12,110 C220,205 470,178 730,96 C940,32 1090,48 1192,125 C1070,72 930,64 730,116 C470,182 230,196 12,110Z" fill="url(#waveBand)"/>
  </svg>
</section>

<section class="about">
  <p class="abs about-eyebrow">ABOUT</p>
  <h2 class="abs about-title">THE FUTURE IS EXCITING</h2>
  <div class="abs about-text">
    <p>Let's make the electricity system smarter together. Vindgerdi uses artificial intelligence, data science and automation to minimize costs and promote eccentricity.</p>
    <p>Let's make the electricity system smarter together. Vindgerdi uses artificial intelligence, data science and automation to minimize costs and promote eccentricity.</p>
  </div>
  <div class="abs btn-dark">READ MORE</div>
  <div class="abs about-visual" role="img" aria-label="Engineer standing in a control room surrounded by data monitors"></div>
</section>

<section class="abs panel panel-price" role="group" aria-label="Price list">
  <div class="abs panel-icon" role="img" aria-label="Hand holding a flame icon" style="width:95px;height:95px;border:3px solid #fff;border-radius:50%"></div>
  <h3 class="abs panel-title">PRICE LIST</h3>
  <div class="abs price-pills">
    <div class="price-pill"><span class="price-value">6.95</span><span class="price-unit">ISK / kWh</span></div>
    <div class="price-pill"><span class="price-value">6.22</span><span class="price-unit">ISK / kWh</span></div>
  </div>
  <p class="abs price-label">Electric Acceleration</p>
  <p class="abs price-link">Make a price comparison</p>
  <div class="abs btn-light">VERDSJA</div>
</section>

<section class="abs panel panel-business" role="group" aria-label="Welcome to business">
  <svg class="abs panel-icon" width="88" height="82" viewBox="0 0 88 82" fill="none" stroke="#fff" stroke-width="5" stroke-linecap="round">
    <path d="M24 14 A32 32 0 0 0 20 66"/><path d="M16 10 l10 3 -4 9"/>
    <path d="M64 68 A32 32 0 0 0 68 16"/><path d="M72 72 l-10 -3 4 -9"/>
    <path d="M52 4 L30 44 H46 L38 78 L62 36 H46 Z" fill="#fff" stroke-width="2"/>
  </svg>
  <h3 class="abs panel-title">WELCOME TO BUSINESS</h3>
  <p class="abs biz-heading" style="top:250px">Company</p>
  <p class="abs biz-text" style="top:296px">We are focused on tech by using optimization and machine learning to minimize electricity prices to our customers.</p>
  <p class="abs biz-heading" style="top:370px">Home</p>
  <p class="abs biz-text" style="top:416px;font-size:13.5px">Our marketing strategy is to portray a tech company mindset and to show dedication to driving down the electricity price on the market.</p>
</section>

<section class="faq">
  <p class="abs faq-eyebrow">OUR</p>
  <h2 class="abs faq-title">QUESTION &amp; ANSWER</h2>
  <ul class="abs faq-list">
    <li class="faq-item">Can anyone buy electricity from Vindgerdi?<span class="faq-toggle"><svg width="20" height="20" viewBox="0 0 20 20" stroke="#fff" stroke-width="2.5"><path d="M10 1v18M1 10h18"/></svg></span></li>
    <li class="faq-item">How do I buy electricity from Vindgerdi?<span class="faq-toggle"><svg width="20" height="20" viewBox="0 0 20 20" stroke="#fff" stroke-width="2.5"><path d="M10 1v18M1 10h18"/></svg></span></li>
    <li class="faq-item">What happens after I sign up for a business?<span class="faq-toggle"><svg width="20" height="20" viewBox="0 0 20 20" stroke="#fff" stroke-width="2.5"><path d="M10 1v18M1 10h18"/></svg></span></li>
    <li class="faq-item">The future with Vindgerdi?<span class="faq-toggle"><svg width="20" height="20" viewBox="0 0 20 20" stroke="#fff" stroke-width="2.5"><path d="M10 1v18M1 10h18"/></svg></span></li>
  </ul>
</section>

<footer class="abs footer">
  <div class="abs footer-brand">
    <span class="brand-dot"></span>
    <span class="brand-name">VINDGERDI</span>
  </div>
  <div class="abs footer-contacts">
    <div class="contact">
      <span class="contact-icon"><svg width="20" height="20" viewBox="0 0 24 24" fill="none" stroke="#2a2a2a" stroke-width="2"><rect x="3" y="5" width="18" height="14" rx="1"/><path d="M3 6l9 7 9-7"/></svg></span>
      hallo@vindgerdi-example.is
    </div>
    <div class="contact">
      <span class="contact-icon"><svg width="20" height="20" viewBox="0 0 24 24" fill="none" stroke="#2a2a2a" stroke-width="2"><path d="M5 3h4l2 5-3 2a11 11 0 0 0 6 6l2-3 5 2v4a2 2 0 0 1-2 2A17 17 0 0 1 3 5a2 2 0 0 1 2-2z"/></svg></span>
      555-0142
    </div>
  </div>
  <div class="abs footer-rule"></div>
  <p class="abs copyright">Copyrights @ 2021 Vindgerdi. All Rights Reserved.</p>
</footer>

</body>
</html>
```